Business Card Design Can you design a business card design? Looking for something unique and differe

Can you design a business card design? Looking for something unique and different. Can you design a business card design? Looking for something unique and different.Can you design a business card design? Looking for something unique and different.Can you design a business card design? Looking for something unique and different.Can you design a business card design? Looking for something unique and different.Can you design a business card design? Looking for something unique and different.

Industry/Entity Type

Business

Contact Information for Business Card

Can you design a business card design? Looking for something unique and different.

Font styles to use
Serif

```html
<!DOCTYPE html>
<html lang="en">
<head>
<meta charset="utf-8">
<title>Dosewell — Business Card</title>
<link rel="stylesheet" href="https://fonts.googleapis.com/css2?family=Open+Sans:wght@400;600;700&display=swap">
<style>
  :root {
    --stage: #ecebee;
    --card: #ffffff;
    --purple: #8c6aa3;
    --purple-back: #9076a2;
    --grey: #9c9c9f;
    --ink: #3a3a3d;
    --white: #ffffff;
  }
  * { box-sizing: border-box; margin: 0; padding: 0; }
  html, body {
    width: 1200px; height: 1200px; overflow: hidden;
    background: var(--stage);
    font-family: "Open Sans", Arial, sans-serif;
  }
  .canvas {
    position: relative; width: 1200px; height: 1200px;
  }
  .card {
    position: absolute; left: 180px; width: 840px; height: 480px;
    overflow: hidden;
    box-shadow: 0 8px 24px rgba(0,0,0,0.12);
  }
  .card--back { top: 90px; background: var(--purple-back); }
  .card--front { top: 630px; background: var(--card); }

  .back-brand {
    position: absolute; inset: 0;
    display: flex; align-items: center; justify-content: center;
    color: var(--white); font-weight: 700; font-size: 72px; letter-spacing: 1px;
  }

  .card-bands { position: absolute; inset: 0; }

  .holder { position: absolute; left: 92px; top: 26px; }
  .holder-name { color: var(--purple); font-weight: 700; font-size: 28px; line-height: 1.15; }
  .holder-title { color: var(--ink); font-size: 19px; line-height: 1.3; }

  .contact {
    position: absolute; left: 42px; top: 196px;
    color: var(--ink); font-size: 17px; line-height: 1.35;
    list-style: none;
  }
  .contact .gap { margin-top: 14px; }
  .contact .label { color: var(--purple); }

  .front-brand {
    position: absolute; left: 440px; top: 230px; width: 330px;
    display: flex; align-items: center; justify-content: center; gap: 14px;
    color: var(--purple); font-weight: 700; font-size: 48px;
  }
  .front-brand .mark {
    width: 34px; height: 34px; background: var(--purple);
  }
</style>
</head>
<body>
<main class="canvas">

  <section class="card card--back" aria-label="Card back">
    <div class="back-brand">Dosewell</div>
  </section>

  <section class="card card--front" aria-label="Card front">
    <svg class="card-bands" width="840" height="480" viewBox="0 0 840 480" aria-hidden="true">
      <polygon points="0,28 48,28 36,52 0,52" fill="var(--purple)"/>
      <polygon points="54,28 78,28 66,52 42,52" fill="var(--grey)"/>
      <polygon points="0,398 352,398 364,414 0,414" fill="var(--purple)"/>
      <polygon points="384,398 840,398 840,480 330,480" fill="var(--grey)"/>
    </svg>

    <div class="holder">
      <p class="holder-name">Clara Wendt</p>
      <p class="holder-title">Managing Director</p>
    </div>

    <ul class="contact">
      <li>12345, Address Goes Here</li>
      <li>Country Name, 123456</li>
      <li class="gap"><span class="label">p:</span> 021-555 014 362</li>
      <li><span class="label">f:</span> 021-555 014 363</li>
      <li><span class="label">e:</span> hello@dosewell.example</li>
    </ul>

    <div class="front-brand">
      <span class="mark" aria-hidden="true"></span>
      <span>Dosewell</span>
    </div>
  </section>

</main>
</body>
</html>
```